Need Business Card for our Real Estate Business with Sales Executive's Picture

PANTONE 484 C ( RED)

PANTONE 2766 C ( BLUE

Industry/Entity Type

Real Estate

Contact Information for Business Card

Name, Mobile, email, & picture of Person
Agency Phone, address, Web address

Requirements
Must have
• Our Logo Colours, Agent Picture,

```html
<!DOCTYPE html>
<html lang="en">
<head>
<meta charset="utf-8">
<title>Meridian Real Estate – Business Card</title>
<link href="https://fonts.googleapis.com/css2?family=Open+Sans:wght@400;600;700&display=swap" rel="stylesheet">
<style>
  :root{
    --navy:#1a2b5e;
    --red:#b5262f;
    --white:#ffffff;
    --paper:#e4e4e4;
    --ink:#1a2b5e;
  }
  *{margin:0;padding:0;box-sizing:border-box}
  html,body{width:1200px;height:852px;overflow:hidden}
  body{background:var(--paper);font-family:"Open Sans",Arial,sans-serif;position:relative}
  .card{position:absolute;top:276px;width:520px;height:300px;border-radius:22px;overflow:hidden;box-shadow:0 6px 16px rgba(0,0,0,.18)}
  .card-front{left:50px;background:var(--navy);color:var(--white)}
  .card-back{left:630px;background:var(--white)}

  /* front */
  .front-brand{position:absolute;left:0;right:0;top:92px;text-align:center}
  .brand-name{font-size:48px;font-weight:600;letter-spacing:6px;line-height:1}
  .brand-rule{width:250px;height:1px;background:currentColor;margin:10px auto 6px;opacity:.85}
  .brand-sub{font-size:11px;font-weight:400;letter-spacing:3px;line-height:1.2}
  .front-url{position:absolute;left:0;right:0;top:232px;text-align:center;font-size:13px;letter-spacing:.5px}
  .front-url::before,.front-url::after{content:"";position:absolute;top:27px;width:70px;height:3px;background:var(--red)}
  .front-url::before{left:118px}
  .front-url::after{right:118px}
  .brand-dot{display:inline-block;width:10px;height:10px;background:var(--red);margin-right:10px;vertical-align:middle}

  /* back */
  .back-band{position:absolute;left:0;right:0;top:108px;height:140px;background:var(--navy)}
  .back-stripe{position:absolute;left:0;right:0;top:248px;height:5px;background:var(--red)}
  .back-foot{position:absolute;left:0;right:0;bottom:0;height:4px;background:var(--red)}
  .back-brand{position:absolute;left:210px;top:30px;color:var(--ink);text-align:center;width:250px}
  .back-brand .brand-name{font-size:34px;letter-spacing:4px}
  .back-brand .brand-rule{width:190px;margin:6px auto 4px}
  .back-brand .brand-sub{font-size:9px}
  .agent-photo{position:absolute;left:28px;top:100px;width:175px;height:148px;background:linear-gradient(180deg,#c59a7c 0%,#8a6a58 40%,#24366e 70%,#1c2b58 100%)}
  .agent-info{position:absolute;left:226px;top:120px;color:var(--white)}
  .agent-name{font-size:18px;font-weight:700;line-height:22px}
  .agent-title{font-size:11px;line-height:15px;margin-bottom:6px}
  .contact-list{list-style:none;font-size:11.5px;line-height:16px}
  .contact-list li{display:flex;align-items:center;gap:8px}
  .contact-list svg{width:11px;height:11px;flex:none}
  .address{position:absolute;left:0;right:0;top:264px;text-align:center;font-size:13px;line-height:18px;color:var(--ink)}
</style>
</head>
<body>

<section class="card card-front">
  <div class="front-brand">
    <div class="brand-name"><span class="brand-dot"></span>MERIDIAN</div>
    <div class="brand-rule"></div>
    <div class="brand-sub">REAL ESTATE</div>
  </div>
  <div class="front-url">www.meridianhomes.com</div>
</section>

<section class="card card-back">
  <div class="back-band"></div>
  <div class="back-stripe"></div>
  <div class="back-foot"></div>

  <div class="back-brand">
    <div class="brand-name">MERIDIAN</div>
    <div class="brand-rule"></div>
    <div class="brand-sub">REAL ESTATE</div>
  </div>

  <div class="agent-photo" role="img" aria-label="Portrait photo of the sales executive in a navy suit"></div>

  <div class="agent-info">
    <div class="agent-name">Laura Bennett</div>
    <div class="agent-title">Managing Director</div>
    <ul class="contact-list">
      <li><svg viewBox="0 0 12 12"><path d="M2 1h3l1 3-2 1a6 6 0 0 0 3 3l1-2 3 1v3c-6 1-10-3-9-9z" fill="var(--red)"/></svg>555.010.2234</li>
      <li><svg viewBox="0 0 12 12"><rect x="3" y="0.5" width="6" height="11" rx="1" fill="var(--red)"/><rect x="4" y="2" width="4" height="7" fill="var(--navy)"/></svg>555-010-7788</li>
      <li><svg viewBox="0 0 12 12"><rect x="0.5" y="2" width="11" height="8" fill="var(--red)"/><path d="M1 2.5l5 4 5-4" stroke="var(--navy)" fill="none"/></svg>lbennett@meridianhomes.com</li>
      <li><svg viewBox="0 0 12 12"><circle cx="6" cy="6" r="5.5" fill="var(--red)"/><path d="M0.5 6h11M6 0.5v11M6 0.5c-3 3-3 8 0 11M6 0.5c3 3 3 8 0 11" stroke="var(--navy)" stroke-width=".8" fill="none"/></svg>www.meridianhomes.com</li>
    </ul>
  </div>

  <div class="address">418 Cedar Row #210, Fairview, CO 80000</div>
</section>

</body>
</html>
```